Business Card Design For A Renovation Contractor Company

We need a business card for a new company based in Singapore, our company name is "RB Tolvane". We are a renovation contractor that builds designs into reality. We build more of F&B restaurants, retail stores and commercial offices. We work very closely with designers. The final design should communicate to our client that we are a company that you can trust, that will plan and complete your project without giving you a headache. I like my client to remember my company as "RB". The beauty of SIMPLE is important.

Industry/Entity Type

Contractor

Requirements
Nice to have
• Black or Red base

```html
<!DOCTYPE html>
<html lang="en">
<head>
<meta charset="utf-8">
<title>RB Tolvane – Business Card</title>
<link href="https://fonts.googleapis.com/css2?family=Arimo:wght@400;700&display=swap" rel="stylesheet">
<style>
  :root {
    --bg: #e6e6ea;
    --card-white: #ffffff;
    --card-black: #050505;
    --band-grey: #4a4a4c;
    --brand-red: #ec1c24;
    --ink: #1a1a1a;
    --text-light: #ffffff;
  }
  * { box-sizing: border-box; margin: 0; padding: 0; }
  html, body {
    width: 1200px; height: 987px; overflow: hidden;
    background: var(--bg);
    font-family: "Arimo", Arial, sans-serif;
  }
  .canvas { position: relative; width: 1200px; height: 987px; }

  .card {
    position: absolute;
    width: 700px; height: 400px;
    border-radius: 28px;
    overflow: hidden;
    box-shadow: 0 10px 30px rgba(0,0,0,0.15);
  }

  /* Back side */
  .card-back {
    left: 440px; top: 60px;
    background: var(--card-black);
    color: var(--text-light);
    display: flex; flex-direction: column; align-items: center; justify-content: center;
  }
  .back-mark { display: flex; align-items: center; gap: 22px; }
  .back-mark .dot {
    width: 64px; height: 64px; border-radius: 50%;
    background: var(--text-light);
  }
  .back-mark .name { font-size: 64px; font-weight: 400; letter-spacing: 1px; color: var(--text-light); }
  .back-web { margin-top: 48px; font-size: 22px; letter-spacing: 7px; }

  /* Front side */
  .card-front { left: 60px; top: 500px; background: var(--card-white); }
  .front-brand {
    position: absolute; left: 0; right: 0; top: 40px;
    display: flex; flex-direction: column; align-items: center;
  }
  .front-brand .mark { display: flex; align-items: center; gap: 14px; }
  .front-brand .dot { width: 44px; height: 44px; border-radius: 50%; background: var(--brand-red); }
  .front-brand .name { font-size: 52px; color: var(--brand-red); font-weight: 400; line-height: 1; }
  .front-brand .tagline {
    margin-top: 8px; padding: 4px 0 3px;
    border-top: 1px solid var(--ink);
    border-bottom: 1px solid var(--ink);
    font-size: 19px; color: var(--ink); letter-spacing: 1px;
  }

  .band-info {
    position: absolute; left: 0; right: 0; top: 180px; height: 160px;
    background: var(--band-grey); color: var(--text-light);
    display: flex; align-items: center; justify-content: center;
  }
  .address { text-align: right; font-size: 19px; line-height: 1.45; padding-right: 26px; align-self: center; }
  .divider { width: 1px; height: 110px; background: var(--text-light); opacity: 0.8; }
  .contacts { list-style: none; font-size: 20px; line-height: 1.4; padding-left: 26px; }

  .band-name {
    position: absolute; left: 0; right: 0; bottom: 0; height: 60px;
    background: var(--brand-red); color: var(--text-light);
    display: flex; align-items: center; padding-left: 150px;
    font-size: 20px;
  }
  .band-name strong { font-size: 28px; font-weight: 700; margin-right: 6px; }
</style>
</head>
<body>
<main class="canvas">
  <section class="card card-back" aria-label="Card back">
    <div class="back-mark">
      <span class="dot"></span>
      <span class="name">RB Tolvane</span>
    </div>
    <p class="back-web">www.rbtolvane.com</p>
  </section>

  <section class="card card-front" aria-label="Card front">
    <div class="front-brand">
      <div class="mark">
        <span class="dot"></span>
        <span class="name">RB Tolvane</span>
      </div>
      <p class="tagline">designs built into reality</p>
    </div>

    <div class="band-info">
      <p class="address">Door No. Street Name<br>City Name, State, Zip Code</p>
      <span class="divider"></span>
      <ul class="contacts">
        <li>p: 123-456-7890</li>
        <li>c: 123-456-7890</li>
        <li>e: info@rbtolvane.com</li>
        <li>w: www.rbtolvane.com</li>
      </ul>
    </div>

    <div class="band-name"><strong>Your Name,</strong> Title</div>
  </section>
</main>
</body>
</html>
```